Business Card for Multi-Brand Sportswear Company

We are looking for a business card which represents our company and the multiple brands within it.

The company: Fen Athletics (LTD)
The brands: Fen, TavaPuni, ElmStretch, Grit and Rain

Employees using these cards would be representing Fen Athletics, rather than any of the individual brands. You will see a current design within the uploaded files, to give some inspiration. The actual text of the brands is not necessary, but the logos should be on there is some format.

Our creative minds on this are stretched, so we are looking for someone to make this their own, and show us what a good business card should look like.

We may like to get these printed with spot gloss, so keep that in mind with your designs.

www.fenathletics.co.uk

Industry/Entity Type

Business

Contact Information for Business Card

Leo Pemberton-Hale
Operations Manager
(+44) 1632 960 418
Leo@fenathletics.co.uk
www.fenathletics.co.uk

Font styles to use
Sans Serif
Other font styles liked:
• Eurostile

Colors
ffffff

Requirements
Nice to have
• Dark (black) background

```html
<!DOCTYPE html>
<html lang="en">
<head>
<meta charset="utf-8">
<title>Fen Athletics – Business Card</title>
<link rel="stylesheet" href="https://fonts.googleapis.com/css2?family=Lato:wght@400;700&display=swap">
<style>
  :root {
    --backdrop-top: #5a5a5a;
    --backdrop-bottom: #3c3c3c;
    --red-core: #e41d25;
    --red-edge: #8e0a10;
    --silver: #e6e6e6;
    --title-dark: #3a0a0c;
    --white: #ffffff;
    --paper-shade: #e4e4e4;
    --ink: #141414;
    --accent-red: #d9202a;
    --brand-purple: #5e4a6b;
    --brand-grey: #8a8a8a;
  }
  * { margin: 0; padding: 0; box-sizing: border-box; }
  html, body { width: 1200px; height: 900px; overflow: hidden; }
  body {
    position: relative;
    font-family: "Lato", sans-serif;
    background: linear-gradient(180deg, var(--backdrop-top), var(--backdrop-bottom));
  }
  .card {
    position: absolute;
    top: 184px;
    height: 490px;
    border-radius: 14px;
    box-shadow: 0 6px 18px rgba(0,0,0,0.35);
    text-align: center;
  }
  .card-front {
    left: 299px;
    width: 301px;
    background: radial-gradient(ellipse at 50% 55%, var(--red-core) 0%, #c8141b 50%, var(--red-edge) 100%);
    color: var(--white);
  }
  .card-back {
    left: 645px;
    width: 305px;
    background: radial-gradient(ellipse at 50% 45%, var(--paper-shade) 0%, #f3f3f3 45%, var(--white) 75%);
  }
  .front-wordmark {
    position: absolute;
    top: 84px; left: 0; right: 0;
    font-size: 30px;
    font-weight: 700;
    letter-spacing: 0.5px;
    color: var(--silver);
  }
  .holder-name {
    position: absolute;
    top: 214px; left: 0; right: 0;
    font-size: 19px;
    font-weight: 700;
    letter-spacing: 0.6px;
    color: var(--silver);
    text-transform: uppercase;
  }
  .holder-role {
    position: absolute;
    top: 239px; left: 0; right: 0;
    font-size: 13px;
    letter-spacing: 0.4px;
    color: var(--title-dark);
    text-transform: uppercase;
  }
  .contact-list {
    position: absolute;
    top: 300px; left: 0; right: 0;
    font-size: 15px;
    line-height: 21.5px;
  }
  .contact-list b { font-weight: 700; }
  .postal-address {
    position: absolute;
    top: 382px; left: 0; right: 0;
    font-size: 15px;
    line-height: 21.5px;
    font-style: normal;
  }
  .back-wordmark {
    position: absolute;
    top: 230px; left: 0; right: 0;
    display: flex;
    align-items: center;
    justify-content: center;
    gap: 10px;
    font-size: 34px;
    font-weight: 700;
    color: var(--ink);
  }
  .back-wordmark .mark-square {
    width: 14px; height: 14px;
    background: var(--accent-red);
  }
  .brand-row {
    position: absolute;
    bottom: 34px; left: 14px; right: 14px;
    display: flex;
    justify-content: space-between;
    align-items: center;
    font-size: 11px;
    font-weight: 700;
  }
  .brand-fen { color: var(--ink); }
  .brand-grit { color: var(--accent-red); }
  .brand-tava { color: var(--brand-purple); }
  .brand-elm { color: var(--brand-grey); }
</style>
</head>
<body>
  <section class="card card-front">
    <div class="front-wordmark">Fen Athletics</div>
    <h1 class="holder-name">Owen Thackeray</h1>
    <p class="holder-role">Managing Director</p>
    <p class="contact-list">
      <b>M:</b> +44(0)1632 960418<br>
      <b>E:</b> owen@fenathletics.co.uk<br>
      www.fenathletics.co.uk
    </p>
    <address class="postal-address">
      Marsh Yard,<br>
      Hallowby, Fenwick, YO99 4QT
    </address>
  </section>

  <section class="card card-back">
    <div class="back-wordmark"><span class="mark-square"></span>Fen Athletics</div>
    <div class="brand-row">
      <span class="brand-fen">Fen</span>
      <span class="brand-grit">Grit and Rain</span>
      <span class="brand-tava">TavaPuni</span>
      <span class="brand-elm">ElmStretch</span>
    </div>
  </section>
</body>
</html>
```